Business Card for Coastal Tundrabridge Advisory

We need a business card for Coastal Tundrabridge Advisory. The company website address is provided below. The company logo is attached. We provide specialized permafrost services to the mining, transportation, and oil & gas industries. The card should be prepared for:
Matthias Korhonen, PhD.
Coastal Tundrabridge Advisory
PO Box 418259
Quillwater, Alaska 99642
Direct: +1-907-555-0143
Email: mkorhonen@tundrabridgeadvisory.example
Website: www.coastaltundrabridgeadvisory.example

```html
<!DOCTYPE html>
<html lang="en">
<head>
<meta charset="utf-8">
<title>Coastal Tundrabridge Advisory – Business Card</title>
<link rel="stylesheet" href="https://fonts.googleapis.com/css2?family=Roboto:wght@300;400;500;700&display=swap">
<style>
  :root {
    --page: #d8d2c8;
    --card: #111823;
    --ink: #f2f4f7;
    --ink-soft: #c9ced6;
    --rule: #8e96a3;
    --ice: #2aa3dd;
    --ice-deep: #164a6e;
  }
  * { box-sizing: border-box; margin: 0; padding: 0; }
  html, body {
    width: 1200px; height: 780px; overflow: hidden;
    background: var(--page);
    font-family: "Roboto", Arial, sans-serif;
  }
  .sheet {
    width: 1200px; height: 780px;
    display: flex; align-items: center; justify-content: center; gap: 40px;
  }
  .card {
    position: relative;
    width: 540px; height: 309px;
    background: var(--card);
    color: var(--ink);
    border-radius: 4px;
    box-shadow: 0 10px 26px rgba(0,0,0,.28);
    overflow: hidden;
  }

  /* Front: contact face */
  .holder { position: absolute; left: 40px; top: 46px; display: inline-block; }
  .holder-name { font-size: 28px; line-height: 1.1; letter-spacing: .2px; white-space: nowrap; }
  .holder-name .given { font-weight: 700; }
  .holder-name .family { font-weight: 300; }
  .holder-degree { display: block; text-align: right; font-size: 16px; font-weight: 500; margin-top: 4px; }
  .divider { position: absolute; left: 208px; top: 126px; }
  .contacts { position: absolute; left: 248px; top: 140px; list-style: none; }
  .contacts li {
    display: flex; align-items: center; gap: 7px;
    font-size: 11.5px; font-weight: 400; color: var(--ink-soft);
    margin-bottom: 9px; white-space: nowrap;
  }
  .contacts svg { width: 11px; height: 11px; flex: none; }
  .address {
    position: absolute; left: 40px; bottom: 40px;
    font-size: 12.5px; font-weight: 300; color: var(--ink-soft); white-space: nowrap;
  }

  /* Back: brand face */
  .texture {
    position: absolute; inset: 0;
    background: linear-gradient(115deg, rgba(17,24,35,0) 38%, rgba(22,74,110,.55) 62%, rgba(42,163,221,.75) 100%);
  }
  .brand { position: absolute; left: 0; right: 0; top: 84px; text-align: center; }
  .brand-name {
    font-size: 21px; font-weight: 700; letter-spacing: 3px;
    text-transform: uppercase; color: var(--ink); line-height: 1.3;
  }
  .services { position: absolute; left: 18px; right: 18px; bottom: 34px; text-align: center; }
  .services-title { font-size: 12px; font-weight: 500; color: var(--ink); margin-bottom: 6px; }
  .services-text { font-size: 10px; font-weight: 300; color: var(--ink-soft); white-space: nowrap; }
</style>
</head>
<body>
<main class="sheet">

  <section class="card card-front">
    <div class="holder">
      <h1 class="holder-name"><span class="given">Matthias</span> <span class="family">Korhonen</span></h1>
      <span class="holder-degree">PhD</span>
    </div>

    <svg class="divider" width="30" height="110" viewBox="0 0 30 110" aria-hidden="true">
      <line x1="29" y1="0" x2="1" y2="110" stroke="var(--rule)" stroke-width="1"/>
    </svg>

    <ul class="contacts">
      <li>
        <svg viewBox="0 0 24 24" aria-hidden="true"><path fill="var(--ink)" d="M6.6 10.8a15 15 0 0 0 6.6 6.6l2.2-2.2a1 1 0 0 1 1-.25 11.4 11.4 0 0 0 3.6.57 1 1 0 0 1 1 1V20a1 1 0 0 1-1 1A17 17 0 0 1 3 4a1 1 0 0 1 1-1h3.5a1 1 0 0 1 1 1c0 1.25.2 2.45.57 3.6a1 1 0 0 1-.25 1z"/></svg>
        +1-907-555-0143
      </li>
      <li>
        <svg viewBox="0 0 24 24" aria-hidden="true"><rect x="2" y="5" width="20" height="14" rx="1.5" fill="none" stroke="var(--ink)" stroke-width="2"/><path d="M3 6l9 7 9-7" fill="none" stroke="var(--ink)" stroke-width="2"/></svg>
        mkorhonen@tundrabridgeadvisory.example
      </li>
      <li>
        <svg viewBox="0 0 24 24" aria-hidden="true"><circle cx="12" cy="12" r="9.5" fill="none" stroke="var(--ink)" stroke-width="2"/><path d="M2.5 12h19M12 2.5c3 3 3 16 0 19M12 2.5c-3 3-3 16 0 19" fill="none" stroke="var(--ink)" stroke-width="1.6"/></svg>
        www.coastaltundrabridgeadvisory.example
      </li>
    </ul>

    <p class="address">PO Box 418259 Quillwater, Alaska 99642</p>
  </section>

  <section class="card card-back">
    <div class="texture" role="img" aria-label="Repeated company name pattern fading from dark navy into bright ice blue"></div>
    <div class="brand">
      <p class="brand-name">Coastal Tundrabridge<br>Advisory</p>
    </div>
    <div class="services">
      <h2 class="services-title">OUR SERVICES</h2>
      <p class="services-text">We provide specialized permafrost services to the mining, transportation, and oil &amp; gas industries</p>
    </div>
  </section>

</main>
</body>
</html>
```